Business Card Design Project

- makeup artist business card

- original and creative

- Elegant design

- Feel free to come out with cool designs but stick to being elegant and attractive

- Design relates to makeup

- includes name, occupation, contact numbers, email, website

- regular size business card

- round corner card

- double sided

- on 1 side it should just have the website name in the center " moonveilstudio.net "

Industry/Entity Type

Business

Requirements
Must have
• Delia Marsh
Makeup Artist
USA: +1 (415)772-0461
Singapore: +65 82307915
deliamarsh@moonveilstudio.net
www.moonveilstudio.net
Should not have
• nothing cartoon looking.
Pictures of makeup being grab from the internet.. Examples: eyes or lips.

```html
<!DOCTYPE html>
<html lang="en">
<head>
<meta charset="utf-8">
<title>Delia Marsh – Makeup Artist Business Card</title>
<link href="https://fonts.googleapis.com/css2?family=Arimo:wght@400;700&family=Tinos:wght@700&display=swap" rel="stylesheet">
<style>
  :root {
    --backdrop-top: #f7f0f2;
    --backdrop-bottom: #e9dde1;
    --card-white: #ffffff;
    --card-white-edge: #e4e4e4;
    --rose: #c9558f;
    --rose-text: #c2407f;
    --plum: #8c2263;
    --plum-text: #6e1a4e;
    --stripe-line: #f4d6e5;
    --ink: #2b2b2b;
    --white: #ffffff;
  }
  * { margin: 0; padding: 0; box-sizing: border-box; }
  html, body {
    width: 1200px; height: 951px; overflow: hidden;
  }
  body {
    position: relative;
    background: linear-gradient(180deg, var(--backdrop-top), var(--backdrop-bottom));
    font-family: "Arimo", Arial, sans-serif;
  }
  .card {
    position: absolute;
    width: 640px; height: 366px;
    border-radius: 30px;
    overflow: hidden;
    box-shadow: 0 10px 28px rgba(90, 40, 60, 0.18);
  }
  /* Website side */
  .card--front {
    left: 120px; top: 90px;
    background: linear-gradient(160deg, var(--card-white) 55%, #f1f1f1);
    border: 1px solid var(--card-white-edge);
    display: flex; align-items: center; justify-content: center;
  }
  .front-line {
    display: flex; align-items: center; gap: 16px;
  }
  .dots { display: flex; align-items: center; gap: 9px; }
  .dots span {
    display: block; border-radius: 50%; background: var(--rose-text);
  }
  .front-url {
    font-size: 33px; color: var(--ink); letter-spacing: 0.2px;
  }
  .front-url .domain { color: var(--rose-text); }

  /* Contact side */
  .card--back {
    left: 440px; top: 495px;
    background: var(--rose);
  }
  .stripe {
    position: absolute; top: 0; bottom: 0; left: 52px; width: 60px;
    background: var(--plum);
    border-left: 4px solid var(--stripe-line);
    border-right: 4px solid var(--stripe-line);
    box-shadow: 0 0 0 7px var(--rose) inset;
  }
  .stripe::before, .stripe::after {
    content: ""; position: absolute; top: 0; bottom: 0; width: 3px;
    background: var(--stripe-line);
  }
  .stripe::before { left: -14px; }
  .stripe::after { right: -14px; }
  .identity {
    position: absolute; right: 48px; top: 78px; text-align: right;
  }
  .identity .name {
    font-family: "Tinos", "Times New Roman", serif;
    font-weight: 700; font-size: 29px; color: var(--white);
  }
  .identity .role {
    font-size: 18px; color: var(--plum-text); margin-top: 2px;
  }
  .contacts {
    position: absolute; left: 160px; top: 232px;
    list-style: none; color: var(--white); font-size: 19px;
  }
  .contacts li {
    display: flex; align-items: center; gap: 10px; height: 25px;
  }
  .contacts svg { width: 16px; height: 16px; flex: none; }
</style>
</head>
<body>

  <section class="card card--front" aria-label="Business card, website side">
    <div class="front-line">
      <div class="dots" aria-hidden="true">
        <span style="width:4px;height:4px"></span>
        <span style="width:5px;height:5px"></span>
        <span style="width:6px;height:6px"></span>
        <span style="width:7px;height:7px"></span>
        <span style="width:8px;height:8px"></span>
      </div>
      <p class="front-url">www.<span class="domain">moonveilstudio</span>.net</p>
      <div class="dots" aria-hidden="true">
        <span style="width:8px;height:8px"></span>
        <span style="width:7px;height:7px"></span>
        <span style="width:6px;height:6px"></span>
        <span style="width:5px;height:5px"></span>
        <span style="width:4px;height:4px"></span>
      </div>
    </div>
  </section>

  <section class="card card--back" aria-label="Business card, contact side">
    <div class="stripe" aria-hidden="true"></div>
    <div class="identity">
      <p class="name">Delia Marsh</p>
      <p class="role">Makeup Artist</p>
    </div>
    <ul class="contacts">
      <li>
        <svg viewBox="0 0 16 16" aria-hidden="true"><circle cx="8" cy="8" r="7.5" fill="#fff"/><path d="M5 4.5c1 0 1.5 1.8 1 2.4-.4.4.7 2 1.6 2.6.6-.4 2.2 0 2.2 1 0 .8-1.4 1.4-2.4.7C5.8 10 4.2 8 4.3 6c0-.8.2-1.5.7-1.5z" fill="#c9558f"/></svg>
        <span>USA: +1 (415)772-0461</span>
      </li>
      <li>
        <svg viewBox="0 0 16 16" aria-hidden="true"><circle cx="8" cy="8" r="7.5" fill="#fff"/><path d="M5 4.5c1 0 1.5 1.8 1 2.4-.4.4.7 2 1.6 2.6.6-.4 2.2 0 2.2 1 0 .8-1.4 1.4-2.4.7C5.8 10 4.2 8 4.3 6c0-.8.2-1.5.7-1.5z" fill="#c9558f"/></svg>
        <span>Singapore: +65 82307915</span>
      </li>
      <li>
        <svg viewBox="0 0 16 16" aria-hidden="true"><circle cx="8" cy="8" r="7.5" fill="#fff"/><rect x="3.5" y="5" width="9" height="6.5" fill="none" stroke="#c9558f" stroke-width="1.2"/><path d="M3.5 5l4.5 3.6L12.5 5" fill="none" stroke="#c9558f" stroke-width="1.2"/></svg>
        <span>deliamarsh@moonveilstudio.net</span>
      </li>
      <li>
        <svg viewBox="0 0 16 16" aria-hidden="true"><circle cx="8" cy="8" r="7.5" fill="#fff"/></svg>
        <span>www.moonveilstudio.net</span>
      </li>
    </ul>
  </section>

</body>
</html>
```